San Francisco Leading Consulting firm - 47Vora Web Design Project

•Create a Web Design
•Uncoded webpage layout design
•2 Pages Design - Homepage + Interior Page

Task Description
Hello, we're looking for a re-design our current website www.47vora-example.com

we have a sample mockup design @

http://47vora.pubtrellis-example.org/

This shows the layout that we like and also a sample of 6 pictures that would change based on where you mouse over..

6 pictures HOME design needs to be included.

SMART
THOUGHTFUL
FLEXIBLE
CREATIVE SERVICES
TECHNICAL SERVICES
PARTNERS

sites we like:

http://www.melvanadvisory-example.com/Home.cfm?id=Home
http://www.plinthworks-example.com/index.html

Our company can be best described as: 100+ employees, cutting-edge, depandable, innovative, strong, smart.

Our Primary focus is: IT Consulting Services and Creative Design services

47Vora LLC is a consulting firm providing creative design, business and technology solutions to both private and public interests.

Established in 1996, 47Vora is a San Francisco based company providing specialists for a range of business needs including:

Creative Design Services
•Print
•Logo Design
•Website Design
•Illustration

and

Business and Technology solutions

•Application Software and Web Development
•Business Process Re-Design (BPR)
•Business/Systems Analysis and Requirement Documentation
•Mentoring and Training
•Network/Hardware Installation Services
•System Design and Architecture
•Vendor Management
•Docuvault Architecture and Implementation

our sample mockup site:

Reason: Due to holiday season, we're not available to work with designers and finilize our design.  

Thank you very much for submitting your design.

We appreciate your time and creativity.   Since, our office is currently closed for holidays, we will be reviewing it in details next week and will make our decision as soon as possible.

It would be great if you could submit any of your changes by Wed next week, so it would be part of our reviews. 

Please see updated wireframe under attachments:  we have some minor updates to our wireframe that we would like you to update your designs, if possible.  

We also encorouge you not to use our standard wireframe and come up with more unique designs.   Everything would be considered when we review your design.

 

Target Market(s)

Creative services and professional services clients, including government agencies

Industry/Entity Type

Business

Requirements
Must have
• Clean, professional look, easy navigation

```html
<!DOCTYPE html>
<html lang="en">
<head>
<meta charset="utf-8">
<title>47Vora — Company</title>
<link href="https://fonts.googleapis.com/css2?family=Roboto+Condensed:wght@300;400&family=Arimo:wght@400;700&display=swap" rel="stylesheet">
<style>
  :root {
    --blue: #2f8fcf;
    --blue-pale: #e8f4fb;
    --line: #cfe4f1;
    --ink: #3a3a3a;
    --grey: #6a6a6a;
    --olive: #8a9a12;
    --olive-dark: #6f7d0c;
  }
  * { box-sizing: border-box; margin: 0; padding: 0; }
  html, body { width: 1200px; height: 730px; overflow: hidden; background: #fff; }
  body { position: relative; font-family: "Arimo", Arial, sans-serif; color: var(--ink); }
  .abs { position: absolute; }

  .brand { left: 224px; top: 20px; display: flex; align-items: center; gap: 10px; }
  .brand-dot { width: 26px; height: 26px; border-radius: 50%; background: var(--blue); }
  .brand-name { font-family: "Roboto Condensed", sans-serif; font-weight: 300; font-size: 30px; color: #333; letter-spacing: 1px; }

  .nav { left: 440px; top: 0; width: 536px; height: 78px; display: flex; border-right: 1px solid var(--line); border-bottom-right-radius: 8px; }
  .nav a { font-family: "Roboto Condensed", sans-serif; font-size: 13px; color: var(--blue); text-decoration: none;
           display: flex; align-items: center; justify-content: center; height: 100%; border-left: 1px solid var(--line); padding-bottom: 4px; }
  .nav a.active { background: var(--blue-pale); }

  .hero-frame { left: 216px; top: 78px; width: 760px; height: 340px; border: 1px solid var(--line); border-top: none; border-radius: 0 0 8px 8px; }
  .hero-photo { left: 224px; top: 87px; width: 752px; height: 275px; border-radius: 8px;
                background: linear-gradient(90deg, #2d3440 0%, #5d6570 35%, #cfcfcc 60%, #dcdcd8 80%, #8a9095 100%); }
  .hero-dots { left: 232px; top: 95px; display: flex; gap: 7px; }
  .hero-dots span { width: 13px; height: 13px; border-radius: 50%; background: rgba(255,255,255,.35); }
  .hero-dots span:nth-child(2) { background: rgba(255,255,255,.8); }
  .hero-title { left: 680px; top: 98px; font-family: "Roboto Condensed", sans-serif; font-size: 46px; color: #333; line-height: 1; letter-spacing: -1px; }
  .hero-sub { left: 680px; top: 147px; width: 280px; font-family: "Roboto Condensed", sans-serif; font-size: 22px; color: #444; line-height: 22px; }
  .hero-pointer { left: 405px; top: 362px; width: 0; height: 0; border-left: 7px solid transparent; border-right: 7px solid transparent; border-top: 7px solid #d0d4d8; }

  .thumb { top: 370px; width: 112px; height: 40px; border: 1px solid #c9d6de; border-radius: 5px;
           background: linear-gradient(180deg, #e2e2e0, #c4c6c4); display: flex; align-items: center; justify-content: center;
           font-family: "Roboto Condensed", sans-serif; font-size: 14px; color: #222; }

  .features { left: 216px; top: 418px; width: 760px; height: 167px; border: 1px solid var(--line); border-top: none; border-radius: 0 0 8px 8px; }
  .divider { top: 418px; width: 1px; height: 167px; background: var(--line); }
  .feat-head { top: 428px; font-family: "Roboto Condensed", sans-serif; font-size: 17px; color: var(--blue); }
  .feat-img { top: 458px; width: 72px; height: 120px; border: 1px solid #c9d6de; border-radius: 6px; }
  .feat-title { top: 460px; font-size: 13px; font-weight: 700; color: #555; }
  .feat-body { top: 483px; width: 142px; font-size: 10px; line-height: 16.8px; color: var(--grey); }

  .btn { top: 596px; width: 84px; height: 18px; border-radius: 9px; background: var(--olive); display: flex; align-items: center;
         font-family: "Roboto Condensed", sans-serif; font-size: 11px; color: #fff; overflow: hidden; }
  .btn span { flex: 1; text-align: center; }
  .btn i { width: 18px; height: 100%; background: var(--olive-dark); display: flex; align-items: center; justify-content: center; font-style: normal; font-size: 9px; }

  .footer-rule { left: 224px; top: 658px; width: 752px; height: 1px; background: #e4e4e4; }
  .footer { left: 0; top: 666px; width: 1200px; text-align: center; font-family: "Roboto Condensed", sans-serif; font-size: 11px; color: #555; }
</style>
</head>
<body>
  <div class="abs brand"><span class="brand-dot"></span><span class="brand-name">47VORA</span></div>

  <nav class="abs nav">
    <a style="width:56px">HOME</a>
    <a class="active" style="width:70px">COMPANY</a>
    <a style="width:124px">TECHNICAL SERVICES</a>
    <a style="width:119px">CREATIVE SERVICES</a>
    <a style="width:73px">PARTNERS</a>
    <a style="width:94px">CONTACT US</a>
  </nav>

  <div class="abs hero-frame"></div>
  <div class="abs hero-photo" role="img" aria-label="Businessman in a suit thinking at a desk beside a laptop"></div>
  <div class="abs hero-dots"><span></span><span></span><span></span><span></span><span></span><span></span></div>
  <div class="abs hero-title">THOUGHFUL</div>
  <div class="abs hero-sub">Lorem ipsum dolor sit amet cusin.</div>
  <div class="abs hero-pointer"></div>

  <div class="abs thumb" style="left:224px">SMART</div>
  <div class="abs thumb" style="left:352px">FLEXIBLE</div>
  <div class="abs thumb" style="left:479px">THOUGHFUL</div>
  <div class="abs thumb" style="left:608px">SMART</div>
  <div class="abs thumb" style="left:736px">SMART</div>
  <div class="abs thumb" style="left:863px">SMART</div>

  <div class="abs features"></div>
  <div class="abs divider" style="left:470px"></div>
  <div class="abs divider" style="left:729px"></div>

  <div class="abs feat-head" style="left:233px">FOR GRAPHIC DESIGNERS</div>
  <div class="abs feat-img" style="left:234px;background:linear-gradient(180deg,#1c2a36,#4a5a62 60%,#b89a6a)" role="img" aria-label="Designer sitting in a cardboard box"></div>
  <div class="abs feat-title" style="left:323px">Get Creative!</div>
  <div class="abs feat-body" style="left:324px">47Vora is looking for top creative talent to deliver graphic design solutions for some leading global brands Do you have what it takes?</div>

  <div class="abs feat-head" style="left:479px">FOR CLIENTS</div>
  <div class="abs feat-img" style="left:480px;background:linear-gradient(180deg,#c9d3da,#8aa0b0 60%,#e8e8e6)" role="img" aria-label="Colleagues meeting around a table"></div>
  <div class="abs feat-title" style="left:570px">The 47Vora Difference</div>
  <div class="abs feat-body" style="left:570px">Smart, Flexible, Thoughtful: find out why leading corporations and government agencies are turning to 47vora to help manage their most demanding IT services challenges.</div>

  <div class="abs feat-head" style="left:738px">FOR PARTNERS</div>
  <div class="abs feat-img" style="left:739px;background:linear-gradient(180deg,#d8dee4,#4a5a72 65%,#c8ccd0)" role="img" aria-label="Business partners shaking hands"></div>
  <div class="abs feat-title" style="left:828px">Team Up With the Best</div>
  <div class="abs feat-body" style="left:829px">When it comes to technology partnerships, our mission it so make you a success.</div>

  <div class="abs btn" style="left:386px"><span>LEARN MORE</span><i>›</i></div>
  <div class="abs btn" style="left:645px"><span>LEARN MORE</span><i>›</i></div>
  <div class="abs btn" style="left:892px"><span>LEARN MORE</span><i>›</i></div>

  <div class="abs footer-rule"></div>
  <div class="abs footer">Copyright 2010, 47Vora, LLC All rights reserved.</div>
</body>
</html>
```